Colin Vardek Business card

Hey there, I’m hoping to have a business card designed. I’m in Real estate and just switched to a new Brokerage called: The Harbourline Property Group

The back could just be the company name maybe or whatever looks good!

I’ve attached some logos of our company and some cards my buddy had done up.

On the card:
Colin Vardek
colinvardek@mailora.com
587-412-9065
colinvardek.ca

Target Market(s)

Home buyers and sellers

Industry/Entity Type

Real Estate

Contact Information for Business Card

just looking for a cool and modern design with my picture on it. I like the idea of Black and red being used.

Requirements
Must have
• all the details provided. I'm open to anything. Just want a professional looking card.

```html
<!DOCTYPE html>
<html lang="en">
<head>
<meta charset="utf-8">
<title>Colin Vardek — Business Card</title>
<link href="https://fonts.googleapis.com/css2?family=Roboto:wght@400;500;700&display=swap" rel="stylesheet">
<style>
  :root {
    --stage: #2b2b2d;
    --card-dark: #252329;
    --pattern-dark: #1f1d22;
    --brand-red: #d0213a;
    --white: #ffffff;
    --photo-top: #3a3a42;
    --photo-bottom: #1c1d24;
  }
  html, body {
    margin: 0;
    width: 1200px;
    height: 852px;
    overflow: hidden;
    background: var(--stage);
    font-family: "Roboto", sans-serif;
  }
  .stage {
    position: relative;
    width: 1200px;
    height: 852px;
  }
  .card {
    position: absolute;
    left: 320px;
    width: 560px;
    height: 320px;
    border-radius: 22px;
    overflow: hidden;
    background: var(--card-dark);
    box-shadow: 0 0 0 3px var(--brand-red);
  }
  .card--back { top: 90px; }
  .card--front { top: 442px; }

  /* Back */
  .back-texture {
    position: absolute;
    inset: 0;
    background: linear-gradient(135deg, var(--card-dark), var(--pattern-dark));
  }
  .back-wordmark {
    position: absolute;
    right: 70px;
    top: 150px;
    display: flex;
    align-items: center;
    gap: 8px;
    color: var(--white);
    font-weight: 700;
    font-size: 15px;
    line-height: 1.1;
    text-transform: uppercase;
    width: 150px;
  }
  .mark-dot {
    flex: none;
    width: 12px;
    height: 12px;
    border-radius: 50%;
    background: var(--brand-red);
  }

  /* Front */
  .red-panel {
    position: absolute;
    left: 0; top: 0; bottom: 0;
    width: 150px;
    background: var(--brand-red);
  }
  .portrait {
    position: absolute;
    left: 110px;
    bottom: 0;
    width: 250px;
    height: 270px;
    background: linear-gradient(180deg, var(--photo-top), var(--photo-bottom));
    border-radius: 110px 110px 0 0;
  }
  .front-wordmark {
    position: absolute;
    right: 36px;
    top: 32px;
    width: 230px;
    color: var(--white);
    font-weight: 700;
    font-size: 24px;
    line-height: 1.05;
    text-transform: uppercase;
    text-align: right;
  }
  .accent-bar {
    position: absolute;
    right: 0;
    top: 140px;
    width: 10px;
    height: 36px;
    background: var(--brand-red);
  }
  .agent-name {
    position: absolute;
    right: 36px;
    top: 146px;
    margin: 0;
    color: var(--brand-red);
    font-weight: 500;
    font-size: 22px;
  }
  .contact-list {
    position: absolute;
    right: 28px;
    top: 200px;
    margin: 0;
    padding: 0;
    list-style: none;
    color: var(--white);
    font-size: 15px;
  }
  .contact-list li {
    display: flex;
    justify-content: flex-end;
    align-items: center;
    gap: 8px;
    margin-bottom: 7px;
  }
  .contact-icon {
    width: 14px;
    height: 14px;
    flex: none;
  }
</style>
</head>
<body>
<main class="stage">

  <section class="card card--back" aria-label="Card back">
    <div class="back-texture" role="img" aria-label="Tone-on-tone repeating brand name texture"></div>
    <div class="back-wordmark"><span class="mark-dot"></span><span>The Harbourline Property Group</span></div>
  </section>

  <section class="card card--front" aria-label="Card front">
    <div class="red-panel"></div>
    <div class="portrait" role="img" aria-label="Portrait photo of Colin Vardek in a dark suit"></div>
    <div class="front-wordmark">The Harbourline Property Group</div>
    <div class="accent-bar"></div>
    <h1 class="agent-name">Colin Vardek</h1>
    <ul class="contact-list">
      <li>587-412-9065
        <svg class="contact-icon" viewBox="0 0 14 14"><circle cx="7" cy="7" r="7" fill="#d0213a"/><path d="M4.5 3.5l1.5 0 .6 2-1 .8a5 5 0 0 0 2.1 2.1l.8-1 2 .6v1.5a1 1 0 0 1-1 1A6 6 0 0 1 3.5 4.5a1 1 0 0 1 1-1z" fill="#fff"/></svg>
      </li>
      <li>colinvardek@mailora.com
        <svg class="contact-icon" viewBox="0 0 14 14"><circle cx="7" cy="7" r="7" fill="#d0213a"/><rect x="3.5" y="4.5" width="7" height="5" fill="#fff"/><path d="M3.5 4.5L7 7.3l3.5-2.8" stroke="#d0213a" stroke-width=".8" fill="none"/></svg>
      </li>
      <li>colinvardek.ca
        <svg class="contact-icon" viewBox="0 0 14 14"><circle cx="7" cy="7" r="7" fill="#d0213a"/><circle cx="7" cy="7" r="3.6" fill="none" stroke="#fff" stroke-width=".9"/><path d="M3.4 7h7.2M7 3.4c-1.8 2-1.8 5.2 0 7.2M7 3.4c1.8 2 1.8 5.2 0 7.2" stroke="#fff" stroke-width=".8" fill="none"/></svg>
      </li>
    </ul>
  </section>

</main>
</body>
</html>
```